Blue Harbor Inc - Cutting-Edge Biotech Laboratory - Sleek & Sophisticated

Please design a website that has more of a high-tech and high-end feel, with contents outlined in the uploaded file.

Please have main tabs of the following categories: Home, About, FDA & LAWS, Science, Products, Media, Contact.

Media can include all the videos and photos.

Current website: www.blueharborlabs.com - it needs to be much more high-end, sleek and more organized. Please do NOT follow the outlines in the old website, but follow the uploaded CONTENT file.

Target Market(s)

doctors

Industry/Entity Type

Biotechnology

Coding

Coded - Design and coding required

Number of Pages Required

5+ page

Requirements
Must have
• Logo
Nice to have
• Some lotion on the website

```html
<!DOCTYPE html>
<html lang="en">
<head>
<meta charset="utf-8">
<title>Blue Harbor Inc</title>
<link href="https://fonts.googleapis.com/css2?family=Montserrat:wght@400;600;700&family=Open+Sans:wght@400;600;700&display=swap" rel="stylesheet">
<style>
:root{
  --navy:#1b2d6b;
  --navy-deep:#0f1c45;
  --blue:#2a4a9a;
  --sky:#6f93cf;
  --pale:#eef2f9;
  --text:#5a6275;
  --white:#ffffff;
}
*{margin:0;padding:0;box-sizing:border-box}
html,body{width:1200px;height:3080px;overflow:hidden;background:var(--white)}
body{font-family:"Open Sans",Arial,sans-serif;color:var(--text);position:relative}
h1,h2,h3,.nav a,.btn,.brand{font-family:"Montserrat",Arial,sans-serif}
.btn{display:inline-block;background:var(--navy);color:var(--white);font-size:13px;font-weight:700;letter-spacing:1px;padding:12px 30px;border-radius:24px;text-decoration:none}
.btn-outline{background:var(--white);color:var(--navy);border:2px solid var(--navy)}
.section-title{text-align:center;color:var(--navy);font-size:34px;font-weight:700;letter-spacing:1px}
.title-rule{width:60px;height:3px;background:var(--navy);margin:12px auto 0}

/* hero */
.hero{position:absolute;left:0;top:0;width:1200px;height:640px;overflow:hidden}
.hero-photo{position:absolute;inset:0;background:linear-gradient(100deg,#f4f6fa 0%,#dfe6f0 45%,#aebdd4 75%,#7d8fae 100%)}
.hero-bar{position:absolute;left:0;top:0;width:100%;height:150px;background:linear-gradient(180deg,rgba(27,45,107,.55),rgba(27,45,107,0))}
.brand{position:absolute;left:100px;top:52px;color:var(--white);font-size:30px;font-weight:700;letter-spacing:1px}
.nav{position:absolute;right:100px;top:62px;display:flex;gap:30px}
.nav a{color:var(--white);font-size:14px;font-weight:600;text-decoration:none}
.hero-copy{position:absolute;left:100px;top:360px}
.hero-copy h1{color:var(--navy);font-size:38px;font-weight:700;line-height:1.35;letter-spacing:.5px}
.hero-copy .btn{margin-top:30px}
.hero-dots{position:absolute;left:560px;top:536px;display:flex;gap:8px}
.hero-dots span{width:12px;height:12px;border-radius:50%;border:2px solid var(--white)}
.hero-dots span:first-child{background:var(--white)}
.hero-curve{position:absolute;left:0;bottom:0}

/* clinical */
.clinical{position:absolute;left:0;top:690px;width:1200px}
.clinical-intro{width:900px;margin:26px auto 0;text-align:center;font-size:14px;line-height:1.7}
.apps{position:absolute;left:100px;top:150px;display:flex;gap:32px}
.app{width:226px}
.app-photo{height:200px;background:linear-gradient(135deg,#d7dee9,#9fb0c8)}
.app:nth-child(2) .app-photo{background:linear-gradient(135deg,#e4d9cf,#a9b6c9)}
.app:nth-child(3) .app-photo{background:linear-gradient(135deg,#e8ddd3,#b9a897)}
.app:nth-child(4) .app-photo{background:linear-gradient(135deg,#e0e6ee,#8fa3bf)}
.app h3{color:var(--blue);font-size:17px;font-weight:700;margin-top:14px}
.arrow{position:absolute;top:240px}

/* about */
.about{position:absolute;left:0;top:1140px;width:1200px;height:420px;background:var(--pale)}
.about-copy{position:absolute;left:100px;top:100px;width:480px}
.about-copy h2{color:var(--navy);font-size:34px;font-weight:700}
.about-copy .title-rule{margin:12px 0 20px}
.about-copy p{font-size:14px;line-height:1.7;margin-bottom:12px}
.about-copy .btn{margin-top:14px}
.video{position:absolute;left:620px;top:100px;width:480px;height:320px;background:linear-gradient(135deg,#4a5f8a,#2a3b63 60%,#1b2d6b)}
.video svg{position:absolute;left:210px;top:130px}

/* team */
.team{position:absolute;left:0;top:1700px;width:1200px}
.cards{position:absolute;left:100px;top:110px;width:1000px}
.card{position:absolute;width:492px;height:300px;background:var(--navy);color:var(--white)}
.card.light{background:var(--sky)}
.card .info{position:absolute;top:48px;width:200px}
.card h3{font-size:20px;font-weight:700}
.card .role{font-size:13px;margin-top:4px;opacity:.9}
.card p{font-size:12px;line-height:1.6;margin-top:14px;opacity:.9}
.card .more{display:block;font-size:13px;font-weight:700;margin-top:14px}
.portrait{position:absolute;top:30px;width:240px;height:240px;border-radius:50%;border:6px solid var(--white);background:linear-gradient(160deg,#dfe5ee,#8c9dba)}
.text-left .info{left:30px}.text-left .portrait{right:24px}
.text-right .info{right:30px}.text-right .portrait{left:24px}
.team-more{position:absolute;left:0;top:760px;width:1200px;text-align:center}

/* footer */
.footer{position:absolute;left:0;top:2580px;width:1200px;height:500px}
.footer-bg{position:absolute;left:0;top:0}
.footer-cols{position:absolute;left:100px;top:120px;width:1000px;color:#c9d2e6}
.fcol{position:absolute;top:0}
.fcol h3{color:var(--white);font-size:17px;font-weight:700;margin-bottom:22px}
.fcol li{list-style:none;font-size:13px;margin-bottom:12px}
.fcol li::before{content:"›";margin-right:10px;color:var(--white)}
.contact-row{display:flex;gap:12px;align-items:flex-start;font-size:13px;line-height:1.5;margin-bottom:14px}
.contact-row svg{flex:none;margin-top:2px}
.news-note{font-size:12px;margin-bottom:12px}
.news-input{width:300px;height:38px;background:var(--white);color:#9aa3b5;font-size:13px;padding:10px 12px}
.news-btn{display:inline-block;margin-top:12px;background:var(--blue);color:var(--white);font-size:12px;font-weight:700;padding:9px 18px;border-radius:3px}
.socials{display:flex;gap:10px;margin-top:16px}
.socials span{width:30px;height:30px;border-radius:50%;background:var(--blue)}
.copyright{position:absolute;left:0;top:440px;width:1200px;text-align:center;font-size:12px;color:#aab5cc}
</style>
</head>
<body>

<header class="hero">
  <div class="hero-photo" role="img" aria-label="Scientist at a laboratory microscope"></div>
  <div class="hero-bar"></div>
  <div class="brand">BLUE HARBOR</div>
  <nav class="nav">
    <a href="#">HOME</a><a href="#">ABOUT</a><a href="#">FDA &amp; LAWS</a><a href="#">SCIENCE</a><a href="#">PRODUCTS</a><a href="#">CONTACT</a>
  </nav>
  <div class="hero-copy">
    <h1>LEADER IN REGENERATIVE MEDICINE<br>INNOVATOR OF THE INDUSTRY</h1>
    <a class="btn" href="#">READ MORE</a>
  </div>
  <div class="hero-dots"><span></span><span></span><span></span><span></span><span></span></div>
  <svg class="hero-curve" width="1200" height="120" viewBox="0 0 1200 120">
    <path d="M0 120 L0 60 Q600 150 1200 20 L1200 120 Z" fill="#ffffff"/>
    <path d="M0 60 Q600 150 1200 20" fill="none" stroke="#1b2d6b" stroke-width="4"/>
  </svg>
</header>

<section class="clinical">
  <h2 class="section-title">OUR CLINICAL APPLICATIONS</h2>
  <div class="title-rule"></div>
  <p class="clinical-intro">Blue Harbor is the producer and distributor of the highest quality umbilical cord, amniotic membrane and placental tissue-based allografts in the industry. Our biologic products are used for a wide variety of clinical applications including:</p>
  <svg class="arrow" style="left:70px" width="16" height="24" viewBox="0 0 16 24"><path d="M12 3 L4 12 L12 21" fill="none" stroke="#1b2d6b" stroke-width="3"/></svg>
  <div class="apps">
    <div class="app"><div class="app-photo" role="img" aria-label="Doctor examining a patient's knee"></div><h3>Orthopedics</h3></div>
    <div class="app"><div class="app-photo" role="img" aria-label="Athlete receiving sports injury treatment"></div><h3>Sports Medicine</h3></div>
    <div class="app"><div class="app-photo" role="img" aria-label="Clinician dressing a wound"></div><h3>Wound Care</h3></div>
    <div class="app"><div class="app-photo" role="img" aria-label="Podiatrist examining a foot"></div><h3>Podiatry</h3></div>
  </div>
  <svg class="arrow" style="left:1114px" width="16" height="24" viewBox="0 0 16 24"><path d="M4 3 L12 12 L4 21" fill="none" stroke="#1b2d6b" stroke-width="3"/></svg>
</section>

<section class="about">
  <div class="about-copy">
    <h2>ABOUT US</h2>
    <div class="title-rule"></div>
    <p>Blue Harbor provides physicians with safe, effective and proven regenerative allografts. Our mission is to help patients heal faster, move better and live fuller lives, and we work closely with doctors across every field of practice.</p>
    <p>We are committed to serving all areas of need in multiple fields, and we have achieved lasting results in helping aging and injured patients recover.</p>
    <a class="btn" href="#">READ MORE</a>
  </div>
  <div class="video" role="img" aria-label="Video interview with the company's founder">
    <svg width="60" height="60" viewBox="0 0 60 60"><circle cx="30" cy="30" r="30" fill="#ffffff"/><path d="M24 18 L42 30 L24 42 Z" fill="#1b2d6b"/></svg>
  </div>
</section>

<section class="team">
  <h2 class="section-title">MEET OUR TEAM</h2>
  <div class="title-rule"></div>
  <div class="cards">
    <div class="card text-left" style="left:0;top:0">
      <div class="info"><h3>Marco Delgado</h3><div class="role">Chief Scientist</div>
      <p>Leads our research team with two decades of lab work in cell biology and tissue science.</p><span class="more">View Details &gt;&gt;</span></div>
      <div class="portrait" role="img" aria-label="Portrait of Marco Delgado"></div>
    </div>
    <div class="card light text-right" style="left:508px;top:0">
      <div class="portrait" role="img" aria-label="Portrait of Lena Hartwell"></div>
      <div class="info"><h3>Lena Hartwell</h3><div class="role">Director of Operations</div>
      <p>Oversees quality, logistics and partner support so every order reaches clinics on time.</p><span class="more">View Details &gt;&gt;</span></div>
    </div>
    <div class="card light text-left" style="left:0;top:316px">
      <div class="info"><h3>Dr. Owen R. Pratt</h3><div class="role">Medical Director, Cardiology</div>
      <p>Guides clinical protocols and trains physicians on safe use of our biologic products.</p><span class="more">View Details &gt;&gt;</span></div>
      <div class="portrait" role="img" aria-label="Portrait of Dr. Owen R. Pratt"></div>
    </div>
    <div class="card text-right" style="left:508px;top:316px">
      <div class="portrait" role="img" aria-label="Portrait of Dr. Nina Castell"></div>
      <div class="info"><h3>Dr. Nina Castell</h3><div class="role">Clinical Advisor</div>
      <p>Brings years of patient care experience and advises on new regenerative applications.</p><span class="more">View Details &gt;&gt;</span></div>
    </div>
  </div>
  <div class="team-more"><a class="btn btn-outline" href="#">VIEW MORE TEAM</a></div>
</section>

<footer class="footer">
  <svg class="footer-bg" width="1200" height="500" viewBox="0 0 1200 500">
    <path d="M0 40 Q600 -30 1200 40 L1200 500 L0 500 Z" fill="#0f1c45"/>
    <path d="M0 420 L1200 420" stroke="#24335f" stroke-width="1"/>
  </svg>
  <div class="footer-cols">
    <div class="fcol" style="left:0;width:260px">
      <h3>Contact us</h3>
      <div class="contact-row"><svg width="14" height="18" viewBox="0 0 14 18"><path d="M7 0 C3 0 0 3 0 7 C0 12 7 18 7 18 C7 18 14 12 14 7 C14 3 11 0 7 0 Z" fill="#ffffff"/><circle cx="7" cy="7" r="2.5" fill="#0f1c45"/></svg><span>4820 Harbor Point Road<br>Brookfield, MA 02140</span></div>
      <div class="contact-row"><svg width="16" height="16" viewBox="0 0 16 16"><path d="M3 1 L6 1 L7 5 L5 6.5 C6 9 7 10 9.5 11 L11 9 L15 10 L15 13 C15 14 14 15 13 15 C6 15 1 10 1 3 C1 2 2 1 3 1 Z" fill="#ffffff"/></svg><span>Marco Delgado (555) 214-3380<br>Lena Hartwell (555) 214-3391</span></div>
      <div class="contact-row"><svg width="16" height="12" viewBox="0 0 16 12"><rect x="0" y="0" width="16" height="12" rx="1" fill="#ffffff"/><path d="M1 1 L8 7 L15 1" fill="none" stroke="#0f1c45" stroke-width="1.5"/></svg><span>info@blueharborlabs.com</span></div>
    </div>
    <div class="fcol" style="left:280px">
      <h3>Quick Links</h3>
      <ul><li>Home</li><li>About us</li><li>Clinical Applications</li><li>Team</li><li>Contact</li></ul>
    </div>
    <div class="fcol" style="left:480px">
      <h3>Other Links</h3>
      <ul><li>FDA &amp; Laws</li><li>Products</li><li>Continuing Services</li><li>Articles</li><li>Treatment Plan</li></ul>
    </div>
    <div class="fcol" style="left:680px">
      <h3>SIGN UP TO NEWSLETTER</h3>
      <div class="news-note">Get our latest research news and product updates.</div>
      <div class="news-input">Enter Email</div>
      <span class="news-btn">SUBSCRIBE</span>
      <div class="socials"><span></span><span></span><span></span><span></span><span></span></div>
    </div>
  </div>
  <div class="copyright">© Copyright 2018 Blue Harbor Inc. All Rights Reserved. &nbsp;|&nbsp; Site map &nbsp;|&nbsp; Privacy policy</div>
</footer>

</body>
</html>
```